Modern, clean and professional Wordpress design for a safety training company!

We are currently in the process of creating a new website for our business. We have hired a website developer and the main structure of our new Wordpress site is complete. We now need an overall design plan for the site. We need a very clean, professional and easy to follow website. Most of our website visitors only spend about 30-45 secs on our sites "shopping " so it is imperative that we have a strong Home Page.
Our company specializes in CPR and First Aid Certification Classes to businesses and individuals throughout Northern California. We provide these certifications two ways: ONSITE-We come to you, and HOSTED-we offer weekly classes at our 2 locations.
Our design needs to use the general green and blue colors of our logo. But we also like white.
The final design MUST communicate a legitimate, trustworthy and professional business. Our industry is VERY competitive and we need to STAND OUT.
Currently, the NEW website that we need a new design for is www.LifelineDrillWorks.com
Our old website is www.RescuePrepValleyHub.com and we really do like the design of this website, but we just needed a Wordpress site for SEO purposes.
These are 3 websites that we really:
http://morvaliontech.com/
http://www.tralbex.com/
https://www.plivant.com/
I have attached our Logo and other images if you need to use them but looking at the current two sites will be you best help.
Target Market(s)
1) Large businesses and industries that are looking for a company to provide ONSITE safety training classes at their office or place of work.
2) Individuals that need certifications for their jobs and other needs. These individuals are looking for a legitimate, trustworthy and professional environment to complete their training class.

```html
<!DOCTYPE html>
<html lang="en">
<head>
<meta charset="utf-8">
<title>Keystone Response Institute</title>
<link href="https://fonts.googleapis.com/css2?family=Ubuntu:wght@400;500&family=Arimo:wght@400;700&display=swap" rel="stylesheet">
<style>
:root{
  --blue:#23409a;
  --green:#8db70f;
  --text:#555;
  --muted:#888;
  --head:#444;
  --rule:#e2e2e2;
  --band:#f5f5f5;
  --footer:#3b3b3b;
  --gold:#f2b72a;
}
*{margin:0;padding:0;box-sizing:border-box}
html,body{width:817px;height:1200px;overflow:hidden;background:#fff}
body{position:relative;font-family:"Arimo",Arial,sans-serif;color:var(--text)}
.abs{position:absolute}
.topline{left:0;top:0;width:817px;height:2px;background:var(--green)}
.brand{left:67px;top:30px;display:flex;align-items:center;gap:7px}
.brand-mark{width:18px;height:18px;border-radius:50%;background:var(--green)}
.brand-name{font-family:"Ubuntu",sans-serif;font-weight:500;font-size:15px;color:var(--blue);line-height:1.15;width:120px}
.search{left:598px;top:19px;width:151px;height:24px;border:1px solid #d8d8d8;font-family:"Ubuntu",sans-serif;font-size:8px;color:#999;padding:6px 8px}
.search svg{position:absolute;right:8px;top:7px}
.nav{left:286px;top:67px;display:flex;gap:24px;font-family:"Ubuntu",sans-serif;font-size:8px;color:#555}
.nav .active{color:var(--green)}
.hero{left:0;top:100px;width:817px;height:341px;background:linear-gradient(180deg,#e8ebee 0%,#c9c6c2 40%,#7b6a5c 75%,#4d4d52 100%)}
.hero-arrow{top:250px;width:38px;height:38px;border:2px solid rgba(255,255,255,.45);border-radius:50%}
.features{left:67px;top:368px;width:682px;height:205px;display:flex}
.feature{width:227.33px;height:205px;color:#fff;text-align:center;padding-top:18px}
.feature.blue{background:var(--blue)}
.feature.green{background:var(--green)}
.feature h3{font-family:"Ubuntu",sans-serif;font-weight:500;font-size:10px;margin-top:10px}
.feature p{font-size:7.2px;line-height:14.6px;margin:12px 16px 0}
.feature .btn{display:inline-block;margin-top:14px;border:1px solid #fff;width:89px;height:26px;line-height:24px;font-family:"Ubuntu",sans-serif;font-weight:500;font-size:9px}
.shadow{left:80px;top:572px;width:657px;height:18px;background:radial-gradient(ellipse at 50% 0%,rgba(0,0,0,.3),rgba(0,0,0,0) 70%)}
.welcome h1{position:absolute;left:0;top:610px;width:817px;text-align:center;font-family:"Ubuntu",sans-serif;font-weight:400;font-size:14.5px;color:var(--head)}
.welcome p{position:absolute;left:140px;top:643px;width:537px;text-align:center;font-size:8.3px;line-height:17px;color:var(--muted)}
.rule{height:1px;background:var(--rule)}
.section-title{font-family:"Ubuntu",sans-serif;font-size:14.5px;color:var(--head)}
.video{left:67px;top:752px;width:246px;height:128px;background:linear-gradient(135deg,#6b5a4a,#9aa7c4 50%,#3b3e5a)}
.play{left:112px;top:43px;width:24px;height:22px;background:rgba(0,0,0,.8);border:1px solid #ddd;border-radius:3px}
.video-bar{left:0;bottom:0;width:100%;height:10px;background:#111}
.small{font-size:6.8px;line-height:13px;color:var(--text)}
.pager{left:722px;top:726px;display:flex;gap:1px}
.pager span{width:13px;height:13px;background:#555;display:flex;align-items:center;justify-content:center}
.news-img{width:90px;height:71px;border:1px solid #ddd}
.news-title{font-size:8px;color:var(--blue)}
.news-date{font-size:7px;font-style:italic;color:var(--green)}
.reviews{left:0;top:969px;width:817px;height:161px;background:var(--band);border-top:1px solid #e6e6e6}
.quote{font-family:"Ubuntu",sans-serif;font-size:22px;color:#888}
.footer{left:0;top:1130px;width:817px;height:70px;background:var(--footer)}
.foot-links{left:67px;top:19px;display:flex;gap:14px;font-size:7.4px;color:#ccc}
.copy{left:67px;top:43px;font-size:7.2px;color:#bbb}
.social{left:648px;top:25px;display:flex;gap:9px}
.social span{width:19px;height:19px;border-radius:50%;background:#777}
</style>
</head>
<body>
<div class="abs topline"></div>

<header>
  <div class="abs brand"><span class="brand-mark"></span><span class="brand-name">Keystone Response Institute</span></div>
  <div class="abs search">SEARCH
    <svg width="9" height="9" viewBox="0 0 10 10"><circle cx="4" cy="4" r="3" fill="none" stroke="#777" stroke-width="1.3"/><line x1="6.3" y1="6.3" x2="9" y2="9" stroke="#777" stroke-width="1.5"/></svg>
  </div>
  <nav class="abs nav">
    <span class="active">HOME</span><span>CLASS CALENDER</span><span>CLASSES FOR GROUPS</span><span>CERTIFICATION CLASSES</span><span>ABOUT US</span><span>POLICIES</span>
  </nav>
</header>

<div class="abs hero" role="img" aria-label="Photo of an instructor presenting to a seated class of students"></div>
<div class="abs hero-arrow" style="left:20px"></div>
<div class="abs hero-arrow" style="left:755px"></div>

<section class="abs features">
  <div class="feature blue">
    <svg width="40" height="36" viewBox="0 0 40 36"><rect x="2" y="8" width="36" height="26" rx="4" fill="#fff"/><rect x="14" y="2" width="12" height="8" rx="2" fill="none" stroke="#fff" stroke-width="2.5"/><rect x="8" y="8" width="2.5" height="26" fill="#23409a"/><rect x="29.5" y="8" width="2.5" height="26" fill="#23409a"/><rect x="17.5" y="13" width="5" height="16" fill="#23409a"/><rect x="12" y="18.5" width="16" height="5" fill="#23409a"/></svg>
    <h3>FIRST AID CERTIFICATION</h3>
    <p>Keystone Response Institute is Northern California's shorter and provide common sense knowledge and skills to each student to help prepare them for actual our classes emergencies.</p>
    <span class="btn">REDA MORE</span>
  </div>
  <div class="feature green">
    <svg width="42" height="36" viewBox="0 0 42 36"><rect x="7" y="5" width="28" height="20" rx="2" fill="none" stroke="#fff" stroke-width="2.5"/><path d="M1 29h40v2a2 2 0 0 1-2 2H3a2 2 0 0 1-2-2z" fill="#fff"/></svg>
    <h3>REGISTER AND PAY ONLINE (CPR)</h3>
    <p>Keystone Response Institute is Northern California's shorter and provide common sense knowledge and skills to each student to help prepare them for actual our classes emergencies.</p>
    <span class="btn">REDA MORE</span>
  </div>
  <div class="feature blue">
    <svg width="40" height="36" viewBox="0 0 40 36"><path d="M26 6H8a4 4 0 0 0-4 4v20a4 4 0 0 0 4 4h20a4 4 0 0 0 4-4V20" fill="none" stroke="#fff" stroke-width="2.5"/><path d="M32 2l5 5-16 16-7 2 2-7z" fill="#fff"/></svg>
    <h3>REGISTER ONLY AND PAY LATER</h3>
    <p>Keystone Response Institute is Northern California's shorter and provide common sense knowledge and skills to each student to help prepare them for actual our classes emergencies.</p>
    <span class="btn">REDA MORE</span>
  </div>
</section>
<div class="abs shadow"></div>

<section class="welcome">
  <h1>WELCOME TO KEYSTONE RESPONSE INSTITUTE!</h1>
  <p>Keystone Response Institute is Northern California's leader in CPR, BLS, and Basic First Aid Certifications! Taught by experienced Fire-fighters, our classes are much shorter and provide common sense knowledge and skills to each student to help prepare them for using real life emergency responders actual emergencies.</p>
</section>

<div class="abs rule" style="left:67px;top:709px;width:682px"></div>

<section>
  <h2 class="abs section-title" style="left:67px;top:724px">VIDEO LIBRARY</h2>
  <div class="abs video" role="img" aria-label="Video still of medical staff treating a patient in a hospital">
    <div class="abs play"><svg width="22" height="20" viewBox="0 0 22 20"><path d="M9 6l6 4-6 4z" fill="#fff"/></svg></div>
    <div class="abs video-bar"></div>
  </div>
  <p class="abs small" style="left:67px;top:889px;width:246px;text-align:justify">Keystone Response Institute is Northern California's leader in CPR, BLS, and Basic First Aid Certifications! Taught by experienced Firefighters, our classes are much shorter and provide common sense knowledge and skills to each student to help prepare them for actual emergencies.</p>
</section>

<section>
  <h2 class="abs section-title" style="left:330px;top:724px">NEWS UPDATES</h2>
  <div class="abs pager">
    <span><svg width="5" height="7" viewBox="0 0 5 7"><path d="M4 0L1 3.5 4 7" fill="none" stroke="#fff"/></svg></span>
    <span><svg width="5" height="7" viewBox="0 0 5 7"><path d="M1 0l3 3.5L1 7" fill="none" stroke="#fff"/></svg></span>
  </div>

  <div class="abs news-img" style="left:332px;top:755px;background:linear-gradient(160deg,#7b9a6c,#b8b4ae 55%,#6d7488)" role="img" aria-label="Photo of a rescuer performing CPR on a person on a street"></div>
  <div class="abs news-title" style="left:435px;top:757px">MORVALION TECH REPORTS SECOND QUARTER FISCAL 2015 RESULTS</div>
  <div class="abs news-date" style="left:435px;top:771px">Posted On FEBRUARY 12, 2015</div>
  <p class="abs small" style="left:435px;top:783px;width:314px;text-align:justify">Keystone Response Institute is Northern California's leader in CPR, BLS, and Basic First Aid Certifications! Taught by experienced Firefighters, our classes are much shorter and provide common sense knowledge and skills to each student to help prepare them for actual emergencies.</p>

  <div class="abs rule" style="left:330px;top:842px;width:419px"></div>

  <div class="abs news-img" style="left:332px;top:865px;background:linear-gradient(160deg,#3f4a3a,#7a6a52 50%,#2f3340)" role="img" aria-label="Photo of responders treating an injured person on the ground"></div>
  <div class="abs news-title" style="left:435px;top:867px">MORVALION TECH REPORTS SECOND QUARTER FISCAL 2015 RESULTS</div>
  <div class="abs news-date" style="left:435px;top:881px">Posted On FEBRUARY 12, 2015</div>
  <p class="abs small" style="left:435px;top:893px;width:314px;text-align:justify">Keystone Response Institute is Northern California's leader in CPR, BLS, and Basic First Aid Certifications! Taught by experienced Firefighters, our classes are much shorter and provide common sense knowledge and skills to each student to help prepare them for actual emergencies.</p>
</section>

<section class="abs reviews">
  <h2 class="abs section-title" style="left:0;top:18px;width:817px;text-align:center">CUSTOMER REVIEWS</h2>
  <span class="abs quote" style="left:106px;top:31px">&ldquo;</span>
  <p class="abs small" style="left:120px;top:54px;width:577px;text-align:center;font-size:7.3px;line-height:15px;color:var(--muted)">Keystone Response Institute is Northern California's leader in CPR, BLS, and Basic First Aid Certifications! Taught by experienced Firefighters, our classes are much shorter and provide common sense knowledge and skills to each student to help prepare them for actual emergencies.</p>
  <span class="abs quote" style="left:622px;top:73px">&rdquo;</span>
  <svg class="abs" style="left:368px;top:93px" width="80" height="16" viewBox="0 0 80 16">
    <g fill="var(--gold)" stroke="#b07a10" stroke-width=".6">
      <polygon points="8,0.5 10.2,5.6 15.5,6 11.4,9.4 12.7,15 8,12 3.3,15 4.6,9.4 0.5,6 5.8,5.6"/>
      <polygon transform="translate(16 0)" points="8,0.5 10.2,5.6 15.5,6 11.4,9.4 12.7,15 8,12 3.3,15 4.6,9.4 0.5,6 5.8,5.6"/>
      <polygon transform="translate(32 0)" points="8,0.5 10.2,5.6 15.5,6 11.4,9.4 12.7,15 8,12 3.3,15 4.6,9.4 0.5,6 5.8,5.6"/>
      <polygon transform="translate(48 0)" points="8,0.5 10.2,5.6 15.5,6 11.4,9.4 12.7,15 8,12 3.3,15 4.6,9.4 0.5,6 5.8,5.6"/>
      <polygon transform="translate(64 0)" points="8,0.5 10.2,5.6 15.5,6 11.4,9.4 12.7,15 8,12 3.3,15 4.6,9.4 0.5,6 5.8,5.6"/>
    </g>
  </svg>
  <div class="abs" style="left:0;top:117px;width:817px;text-align:center;font-family:'Ubuntu',sans-serif;font-size:9.5px;color:var(--green)">Marisa T- CA, United</div>
  <div class="abs" style="left:0;top:132px;width:817px;text-align:center;font-size:7.3px;color:#333">posed 25 Jan 2015</div>
</section>

<footer class="abs footer">
  <div class="abs foot-links">
    <span>Home</span><span>/</span><span>Class Calender</span><span>/</span><span>Classes for Groups</span><span>/</span><span>Certification Classes</span><span>/</span><span>About Us</span><span>/</span><span>Policies</span>
  </div>
  <div class="abs copy">&copy; Copy Rights 2015.KRI. All rights reserved.</div>
  <div class="abs social"><span></span><span></span><span></span><span></span></div>
</footer>
</body>
</html>
```